Book Cover needed for Printed Book entitled "Mile Ten"

The Book's Title is "Mile Ten", the sub-title is "A Neighbor's Handbook for Calm Roadside Meetings with Patrols", and the author is "Desmond Rawle". The front cover may have just the Title, or it may have a combination of the Title, Sub-Title, and Author. We would like to see designs that presents a feeling of peace and cooperation between US Police Officers and Civilians. The cover can include photographs, illustrations, or just words. But the cover should make the viewer want to open the book for more information.

Target Market(s)

Young adults who live in US inner-cities between ages 18 to 30.

Font styles to use
Sans Serif

Colors

Designer to choose colors to be used in the design.

Requirements
Must have
• Most US Police Officers use the phrase "MILE TEN" to tell other officers that the situation is under control and no assistance is needed. And the book will teach Civilians how to safely conduct themselves during police encounters - which will end with the Cops calling in "MILE TEN" to the dispatcher. So, the front cover must have the phrase "MILE TEN" in big bold letters.
Nice to have
• We would like to see designs that present a feeling of peace and cooperation between US Police Officers and Civilians. Pictures and illustrations of people are acceptable but is not required.

```html
<!DOCTYPE html>
<html lang="en">
<head>
<meta charset="UTF-8">
<title>Mile Ten — Book Cover</title>
<link rel="stylesheet" href="https://fonts.googleapis.com/css2?family=Oswald:wght@500;600;700&display=swap">
<style>
  :root {
    --band: #2b2b2d;
    --night: #050505;
    --white: #ffffff;
    --flag-red: #b8242c;
    --flag-blue: #2a3f7a;
    --flag-cream: #d9d2c6;
  }
  html, body {
    margin: 0;
    padding: 0;
    width: 800px;
    height: 1200px;
    overflow: hidden;
    background: var(--night);
  }
  .cover {
    position: relative;
    width: 800px;
    height: 1200px;
    background: var(--night);
    font-family: "Oswald", sans-serif;
    color: var(--white);
    overflow: hidden;
  }
  .title-band {
    position: absolute;
    top: 0;
    left: 0;
    width: 800px;
    height: 440px;
    background: var(--band);
    text-align: center;
  }
  .title {
    margin: 0;
    padding-top: 2px;
    font-weight: 700;
    font-size: 196px;
    line-height: 236px;
    letter-spacing: -2px;
    white-space: nowrap;
    display: flex;
    justify-content: center;
    align-items: center;
    gap: 18px;
  }
  .title-flag {
    display: inline-block;
    width: 96px;
    height: 62px;
    border-radius: 6px;
    background: linear-gradient(135deg, var(--flag-blue) 0 42%, var(--flag-red) 42% 60%, var(--flag-cream) 60% 72%, var(--flag-red) 72%);
  }
  .subtitle {
    margin: 10px 0 0;
    font-weight: 500;
    font-size: 50px;
    line-height: 60px;
  }
  .emblem-art {
    position: absolute;
    left: 0;
    top: 470px;
    width: 800px;
    height: 730px;
    background:
      radial-gradient(ellipse 300px 260px at 250px 300px, rgba(184,36,44,0.85), rgba(184,36,44,0) 70%),
      radial-gradient(ellipse 220px 200px at 330px 170px, rgba(42,63,122,0.9), rgba(42,63,122,0) 70%),
      radial-gradient(ellipse 260px 200px at 200px 420px, rgba(217,210,198,0.55), rgba(217,210,198,0) 70%),
      var(--night);
  }
  .author {
    position: absolute;
    left: 400px;
    top: 1095px;
    margin: 0;
    font-weight: 600;
    font-size: 38px;
    letter-spacing: 1px;
  }
</style>
</head>
<body>
  <main class="cover">
    <header class="title-band">
      <h1 class="title"><span>MILE</span><span class="title-flag" role="img" aria-label="United States flag shaped as a map of the country"></span><span>TEN</span></h1>
      <p class="subtitle">A Neighbor's Handbook<br>for Calm Roadside Meetings<br>with Patrols</p>
    </header>
    <div class="emblem-art" role="img" aria-label="Bald eagle head overlaid with the stars and stripes of the American flag"></div>
    <p class="author">Desmond Rawle</p>
  </main>
</body>
</html>
```